Request for Business Card Design

Hi. My name is Marlene, I am looking for a new business card design for my company, Quarrow Signal Instruments, LLC. I really like the design you did for Tarsel Venture and was hoping you could do something similar using our full logo and our mark. I am also open to any raised texture design using our mark. I have attached our full logo, which would need to be somewhere on the card, as well as the mark in both outline and full form, as well as our brand colors / guide. The card does not have to be white, as long as our logo and mark appear. I actually like darker colored business cards more, but am open to all options. If you are interested in working with me, please let me know. We would also take the business card design into letterhead design if you can do that.

```html
<!DOCTYPE html>
<html lang="en">
<head>
<meta charset="utf-8">
<title>Quarrow Signal Instruments — Business Card</title>
<link rel="stylesheet" href="https://fonts.googleapis.com/css2?family=Open+Sans:wght@400;600;700&display=swap">
<style>
  :root {
    --stage: #232323;
    --brand-blue: #1a9cc4;
    --brand-blue-deep: #137fa3;
    --brand-teal-light: #86d6dc;
    --card-dark: #3e3e40;
    --text-light: #ffffff;
  }
  * { box-sizing: border-box; margin: 0; padding: 0; }
  html, body {
    width: 1200px; height: 780px; overflow: hidden;
    background: var(--stage);
    font-family: "Open Sans", Arial, sans-serif;
  }
  .canvas { position: relative; width: 1200px; height: 780px; }

  .card {
    position: absolute;
    width: 540px; height: 309px;
    border-radius: 3px;
    overflow: hidden;
    box-shadow: 0 14px 30px rgba(0,0,0,.55);
  }

  /* Front */
  .card--front {
    left: 50px; top: 90px;
    background: var(--brand-blue);
    display: flex; align-items: center; justify-content: center; gap: 16px;
  }
  .brand-dot {
    width: 30px; height: 30px; border-radius: 50%;
    background: var(--brand-teal-light);
  }
  .brand-name {
    color: var(--brand-teal-light);
    font-weight: 700; font-size: 25px; letter-spacing: 2px;
    text-transform: uppercase;
  }

  /* Back */
  .card--back {
    left: 610px; top: 380px;
    background: var(--card-dark);
    border-bottom: 6px solid var(--brand-blue);
  }
  .identity {
    position: absolute; left: 60px; top: 92px; text-align: right;
  }
  .identity__name {
    color: var(--brand-blue); font-weight: 700; font-size: 40px; line-height: 1;
  }
  .identity__role {
    color: var(--text-light); font-weight: 600; font-size: 15px; margin-top: 4px;
  }
  .divider {
    position: absolute; left: 230px; top: 70px;
    width: 2px; height: 105px; background: var(--text-light);
  }
  .contacts {
    position: absolute; left: 250px; top: 74px;
    list-style: none;
  }
  .contacts li {
    display: flex; align-items: center; gap: 9px;
    color: var(--text-light); font-size: 13px; line-height: 25px;
  }
  .contacts svg { width: 14px; height: 14px; fill: var(--brand-blue); flex: none; }
  .address {
    position: absolute; left: 0; right: 0; bottom: 34px;
    text-align: center; color: var(--text-light); font-size: 15px;
  }
</style>
</head>
<body>
<main class="canvas">
  <section class="card card--front" aria-label="Card front">
    <span class="brand-dot"></span>
    <span class="brand-name">Quarrow Signal Instruments</span>
  </section>

  <section class="card card--back" aria-label="Card back">
    <div class="identity">
      <p class="identity__name">Marlene</p>
      <p class="identity__role">Director</p>
    </div>
    <span class="divider"></span>
    <ul class="contacts">
      <li>
        <svg viewBox="0 0 24 24" aria-hidden="true"><path d="M6.6 10.8a15 15 0 0 0 6.6 6.6l2.2-2.2c.3-.3.7-.4 1-.2 1.1.4 2.3.6 3.6.6.6 0 1 .4 1 1V20c0 .6-.4 1-1 1A17 17 0 0 1 3 4c0-.6.4-1 1-1h3.5c.6 0 1 .4 1 1 0 1.3.2 2.5.6 3.6.1.3 0 .7-.2 1z"/></svg>
        +001 555 210 4471
      </li>
      <li>
        <svg viewBox="0 0 24 24" aria-hidden="true"><path d="M6 2h10v6H6zM3 9h18v10h-3v3H6v-3H3zm5 6v5h8v-5z"/></svg>
        +001 555 210 4472
      </li>
      <li>
        <svg viewBox="0 0 24 24" aria-hidden="true"><circle cx="12" cy="12" r="10"/></svg>
        www.quarrowsignal.com
      </li>
      <li>
        <svg viewBox="0 0 24 24" aria-hidden="true"><path d="M2 5h20v14H2zm2 2v.5l8 5 8-5V7z"/></svg>
        info@quarrowsignal.com
      </li>
    </ul>
    <p class="address">1180 Fieldstone Parkway • Halden, CO 80990</p>
  </section>
</main>
</body>
</html>
```